Business Card For Halvenmoor Financial Consulting

Hi, I would like a business card designed. Bold, modern.
Please use the same design as the logo. I have also attached the website design to see the overall theme.
Wordmark Font
Color: Hex: #01AEF7

```html
<!DOCTYPE html>
<html lang="en">
<head>
<meta charset="utf-8">
<title>Halvenmoor Financial Consulting – Business Card</title>
<link rel="stylesheet" href="https://fonts.googleapis.com/css2?family=Outfit:wght@400;600&display=swap">
<style>
  :root {
    --blue: #2293d1;
    --navy: #1b2f3b;
    --white: #ffffff;
    --page: #ffffff;
  }
  * { margin: 0; padding: 0; box-sizing: border-box; }
  html, body {
    width: 809px;
    height: 1200px;
    overflow: hidden;
    background: var(--page);
    font-family: "Outfit", sans-serif;
  }
  .card {
    position: absolute;
    left: 225px;
    width: 358px;
    height: 204px;
    overflow: hidden;
  }

  /* Front */
  .card-front { top: 381px; background: var(--blue); }
  .front-band {
    position: absolute; left: 0; top: 123.5px;
    width: 100%; height: 52.3px;
    background: var(--navy);
  }
  .front-column {
    position: absolute; left: 155.3px; top: 0;
    width: 157.5px; height: 190.4px;
    background: var(--navy);
  }
  .front-emblem-area {
    position: absolute; left: 171px; top: 0;
    width: 126.7px; height: 123.5px;
    background: var(--blue);
  }
  .brand {
    position: absolute; left: 166px; top: 157px;
    display: flex; align-items: center; gap: 5px;
  }
  .brand-square {
    width: 19px; height: 19px;
    background: var(--blue);
  }
  .brand-name {
    color: var(--white);
    font-weight: 600;
    font-size: 10.5px;
    line-height: 1.05;
    letter-spacing: 0.06em;
    text-transform: uppercase;
  }

  /* Back */
  .card-back { top: 613px; background: var(--navy); }
  .back-band {
    position: absolute; left: 0; top: 123.5px;
    width: 100%; height: 52.3px;
    background: var(--blue);
  }
  .contact-row {
    position: absolute; left: 144px;
    display: flex; align-items: flex-start; gap: 4.6px;
    color: var(--white);
    font-size: 9.6px;
    line-height: 11.9px;
  }
  .contact-icon { flex: none; width: 17px; height: 17px; margin-top: -2.5px; }
  .row-phone { top: 32.5px; }
  .row-address { top: 54px; }
  .row-email { top: 97.5px; }
  .website {
    position: absolute; left: 165.6px; top: 146.5px;
    color: var(--white);
    font-size: 9.6px;
    line-height: 11.9px;
  }
</style>
</head>
<body>
  <section class="card card-front" aria-label="Business card front">
    <div class="front-band"></div>
    <div class="front-column"></div>
    <div class="front-emblem-area" role="img" aria-label="Large brand emblem decoration"></div>
    <div class="brand">
      <span class="brand-square"></span>
      <span class="brand-name">Halvenmoor<br>Consulting</span>
    </div>
  </section>

  <section class="card card-back" aria-label="Business card back">
    <div class="contact-row row-phone">
      <svg class="contact-icon" viewBox="0 0 20 20" aria-hidden="true">
        <circle cx="10" cy="10" r="10" fill="var(--blue)"/>
        <path d="M6.5 5.2l2 -0.4 1 2.6-1.2 1c.6 1.3 1.6 2.3 2.9 2.9l1-1.2 2.6 1-.4 2c-4.6.2-8.1-3.3-7.9-7.9z" fill="var(--white)"/>
      </svg>
      <span>+1 000 000 0000</span>
    </div>
    <div class="contact-row row-address">
      <svg class="contact-icon" viewBox="0 0 20 20" aria-hidden="true">
        <circle cx="10" cy="10" r="10" fill="var(--blue)"/>
        <path d="M10 4a4 4 0 0 0-4 4c0 3 4 7.5 4 7.5s4-4.5 4-7.5a4 4 0 0 0-4-4z" fill="var(--white)"/>
        <circle cx="10" cy="8" r="1.5" fill="var(--blue)"/>
      </svg>
      <span>000 Lorem ipsum dolor sit amet,<br>consectetuer adipiscing elit, sed<br>United States, State, Zip code</span>
    </div>
    <div class="contact-row row-email">
      <svg class="contact-icon" viewBox="0 0 20 20" aria-hidden="true">
        <circle cx="10" cy="10" r="10" fill="var(--blue)"/>
        <rect x="5" y="6.5" width="10" height="7" rx="0.8" fill="none" stroke="var(--white)" stroke-width="1.2"/>
        <path d="M5.3 7l4.7 3.6 4.7-3.6" fill="none" stroke="var(--white)" stroke-width="1.2"/>
      </svg>
      <span>Email us info@halvenmoorconsulting.com</span>
    </div>
    <div class="back-band"></div>
    <p class="website">WWW.Halvenmoorconsulting.com</p>
  </section>
</body>
</html>
```